Wellness, Meaning, and the Inner Journey Research Program Website

Overview: This website will serve a new research program (Wellness, Meaning, and the Inner Journey) at the Harrowgate University School of Medicine. I want a clean, intuitive design that has a navigation bar, but uses icons/graphic buttons to link to the main pages. In an attached Word document, I have provided a basic information architecture for the site, understanding that this project would just generate graphics and code for the 3 pages. I highlighted the 3 pages I'd like designed.
Target market: People who want to participate in our research, or contribute grant funding to specific projects.
Number of page: The design project focuses on 3 pages, but the site must accommodate 6 pages with top-level links. See attached Word doc.
Logo and website header: Please integrate our logo in the header. I've uploaded it as a png file--both with the name of the website and with just the logo image. I imaging the logo would look great in a banner set against an image of a mountain. The two main design themes I want to see included are nature and healthcare.
Text content: I have not yet provided text. Use some dummy text.
Technical Specifications:
- Build using WordPress. We will host this site ourselves on NetHarbor using WordPress.
- The design package must be coded.
- The template must be responsive to different platforms (e.g., computer, mobile phone, iPad).
Thank you! I look forward to seeing your designs.
- Ned

```html
<!DOCTYPE html>
<html lang="en">
<head>
<meta charset="utf-8">
<title>Wellness, Meaning, and the Inner Journey – Research Program</title>
<link rel="stylesheet" href="https://fonts.googleapis.com/css2?family=Rubik:wght@700;800&family=Lato:wght@400;700&display=swap">
<style>
:root{
  --blue:#135a96;
  --blue-dark:#0f4c82;
  --green:#7aab37;
  --text:#555;
  --ink:#222;
  --light:#f3f3f3;
  --card-label:#e8f0f8;
}
*{box-sizing:border-box;margin:0;padding:0}
html,body{width:1200px;height:3469px;overflow:hidden}
body{position:relative;font-family:'Lato',sans-serif;color:var(--text);background:#fff}
.abs{position:absolute}
.heading{font-family:'Rubik',sans-serif;font-weight:800;color:var(--blue);text-align:center;width:1200px;left:0}
.intro{left:0;width:1200px;text-align:center;font-size:15px;line-height:26px;color:#666}

/* header */
.site-header{top:0;left:0;width:1200px;height:66px;background:rgba(19,90,150,.92);z-index:5}
.brand{top:0;left:0;width:431px;height:66px;background:#f4f4f4;display:flex;align-items:center;padding-left:106px;gap:10px}
.brand-dot{width:30px;height:30px;border-radius:50%;background:var(--green);flex:none}
.brand-name{font-weight:700;font-size:11.5px;color:var(--blue);line-height:14px;white-space:nowrap}
.nav a{position:absolute;top:23px;color:#fff;font-size:14px;text-decoration:none}
.nav a.active{border-bottom:1px solid #fff;padding-bottom:4px}
.search{top:9px;left:936px;width:151px;height:44px;border:1px solid #fff;color:#fff;font-size:13px;padding:13px 16px}
.search svg{position:absolute;right:12px;top:14px}

/* hero */
.hero{top:0;left:0;width:1200px;height:785px;background:
 radial-gradient(ellipse 300px 220px at 370px 330px,#c86a3b 0%,rgba(160,80,50,.5) 50%,transparent 100%),
 radial-gradient(ellipse 500px 200px at 900px 450px,#7b8aa3 0%,transparent 80%),
 linear-gradient(180deg,#2f5486 0%,#5f7fa8 35%,#4f5b6e 60%,#24292c 85%,#1a1d1e 100%)}
.hero-title{top:326px;font-family:'Rubik',sans-serif;font-weight:700;font-size:40px;color:#fff;text-align:center;width:1200px;left:0;text-shadow:0 2px 6px rgba(0,0,0,.5)}
.hero-text{top:385px;left:280px;width:640px;text-align:center;color:#fff;font-size:15px;line-height:32px}
.btn{display:flex;align-items:center;justify-content:center;color:#fff;font-size:15px;font-weight:700;border-radius:30px;background:linear-gradient(180deg,var(--green),#1f5e7a);box-shadow:0 4px 8px rgba(0,0,0,.25);text-transform:uppercase;text-decoration:none}
.arrow{width:52px;height:52px;border-radius:50%;display:flex;align-items:center;justify-content:center}
.dots{top:734px;left:540px;display:flex;gap:11px}
.dots span{width:15px;height:15px;border-radius:50%;border:1.5px solid #fff}
.dots span.on{background:#fff}

/* people */
.person-card{top:994px;width:316px;height:275px;background:#fff;box-shadow:0 0 5px rgba(0,0,0,.25);padding:4px}
.person-card .photo{width:100%;height:100%}
.person-label{top:1286px;width:316px;text-align:center;font-size:17px;color:var(--ink);letter-spacing:.5px}

/* services */
.services{top:1387px;left:0;width:1200px;height:600px;background:linear-gradient(90deg,#f1f1f1 0%,#f2f2f0 50%,#eeeeec 100%)}
.services-art{left:110px;top:1455px;width:518px;height:475px;border-radius:50%;
  background:linear-gradient(135deg,#a9c77f 0%,#6f9a57 30%,#3f6488 60%,#6d737b 100%)}
.services-title{left:655px;top:1488px;font-family:'Rubik',sans-serif;font-weight:800;font-size:42px;color:var(--blue)}
.services-text{left:655px;top:1548px;width:440px;font-size:13px;line-height:27.5px;color:#666}
.service-list{left:655px;top:1680px;list-style:none;font-size:15px;color:var(--ink)}
.service-list li{height:38px;display:flex;align-items:center;gap:6px}

/* research */
.project{top:2193px;width:235px}
.project .photo{height:288px}
.project .label{height:59px;background:var(--card-label);display:flex;align-items:center;justify-content:center;font-size:15px;font-weight:700;color:var(--ink)}
.project.active .label{background:var(--green);color:#fff}

/* faq */
.faq{top:2624px;left:0;width:1200px;height:536px;background:#f6f6f6}
.faq-item{left:170px;width:860px;height:56px;border:1px solid #d6d6d6;background:#fff;font-size:14.5px;color:#555;padding:0 11px;display:flex;align-items:center;justify-content:space-between}
.plus{width:13px;height:13px;background:var(--green);border-radius:2px;position:relative}
.plus:before,.plus:after{content:"";position:absolute;background:#fff}
.plus:before{left:3px;top:6px;width:7px;height:1.5px}
.plus:after{left:5.75px;top:3px;width:1.5px;height:7px}

/* footer */
.site-footer{top:3160px;left:0;width:1200px;height:309px;background:var(--blue)}
.footer-brand{top:3227px;left:0;width:1200px;display:flex;justify-content:center;align-items:center;gap:14px}
.footer-brand .mark{width:46px;height:46px;border-radius:50%;border:2px solid #fff}
.footer-brand .name{font-weight:700;font-size:18px;color:#fff;line-height:22px}
.contact{top:3324px;left:0;width:1200px;display:flex;justify-content:center;gap:48px;color:#fff;font-size:13px}
.contact span{display:flex;align-items:center;gap:5px}
.foot-nav{top:3364px;left:0;width:1200px;display:flex;justify-content:center;gap:29px;font-size:13.5px;color:#fff}
.copy{top:3407px;left:0;width:1200px;text-align:center;color:#fff;font-size:14px}
</style>
</head>
<body>

<!-- hero -->
<section class="hero abs" role="img" aria-label="Sunlit snowy mountain peak at dusk"></section>
<h1 class="hero-title abs">Wellness, Meaning, and the Inner Journey</h1>
<p class="hero-text abs">Lorem ipsum dolor sit amet, consectetur adipiscing elit, sed do eiusmod tempor incididunt ut labore et dolore magna aliqua. Ut enim ad minim veniam,</p>
<a class="btn abs" style="left:500px;top:464px;width:198px;height:51px">Get Started</a>
<div class="arrow abs" style="left:17px;top:400px;background:rgba(19,90,150,.9)"><svg width="14" height="14" viewBox="0 0 14 14"><path d="M9 2 4 7l5 5" fill="none" stroke="#fff" stroke-width="2"/></svg></div>
<div class="arrow abs" style="left:1115px;top:400px;background:rgba(19,90,150,.9)"><svg width="14" height="14" viewBox="0 0 14 14"><path d="M5 2l5 5-5 5" fill="none" stroke="#fff" stroke-width="2"/></svg></div>
<div class="dots abs"><span></span><span></span><span class="on"></span><span></span><span></span></div>

<!-- header -->
<header class="site-header abs">
  <div class="brand abs"><span class="brand-dot"></span><span class="brand-name">Wellness, Meaning, and the Inner Journey<br>The Research Program</span></div>
  <nav class="nav">
    <a class="active" style="left:513px">Home</a>
    <a style="left:580px">People</a>
    <a style="left:652px">Research Projects</a>
    <a style="left:792px">FAQs</a>
    <a style="left:855px">Contact us</a>
  </nav>
  <div class="search abs">Search<svg width="14" height="14" viewBox="0 0 14 14"><circle cx="6" cy="6" r="4.2" fill="none" stroke="#fff" stroke-width="2"/><path d="M9 9l3.5 3.5" stroke="#fff" stroke-width="2"/></svg></div>
</header>

<!-- people -->
<h2 class="heading abs" style="top:860px;font-size:41px">PEOPLE</h2>
<p class="intro abs" style="top:920px">Lorem ipsum dolor sit amet, consectetur adipiscing elit, sed do eiusmod<br>tempor incididunt ut labore et dolore magna aliqua.</p>
<div class="person-card abs" style="left:112px"><div class="photo" role="img" aria-label="Group photo of the research team" style="background:linear-gradient(160deg,#c9c6c0,#4a5e80 55%,#2b3a58)"></div></div>
<div class="person-card abs" style="left:442px"><div class="photo" role="img" aria-label="Committee members meeting in a bright office" style="background:linear-gradient(160deg,#e6e9ec,#9aa2aa 55%,#3e4248)"></div></div>
<div class="person-card abs" style="left:772px"><div class="photo" role="img" aria-label="Partners shaking hands at a meeting" style="background:linear-gradient(160deg,#dcdad6,#7a7f88 50%,#2e3442)"></div></div>
<div class="person-label abs" style="left:112px">RESEARCH TEAM</div>
<div class="person-label abs" style="left:442px">ADVISORY COMMITTEE</div>
<div class="person-label abs" style="left:772px">PARTNERS</div>

<!-- services -->
<section class="services abs" role="img" aria-label="Faded photo of a person working with a calculator"></section>
<div class="services-art abs" role="img" aria-label="Three overlapping photo circles for healthcare, values and spiritual life"></div>
<h2 class="services-title abs">SERVICES</h2>
<p class="services-text abs">Lorem ipsum dolor sit amet, consectetur adipiscing elit, sed do eiusmod tempor incididunt ut labore et dolore magna aliqua. Ut enim ad minim veniam, quis nostrud exercitation ullamco laboris nisi ut aliquip ex ea commodo consequat. Duis aute irure dolor in reprehenderit</p>
<ul class="service-list abs">
  <li><svg width="14" height="14" viewBox="0 0 14 14"><circle cx="7" cy="7" r="7" fill="#7aab37"/><path d="M6 4l3 3-3 3" fill="none" stroke="#fff" stroke-width="1.8"/></svg>Healthcare</li>
  <li><svg width="14" height="14" viewBox="0 0 14 14"><circle cx="7" cy="7" r="7" fill="#7aab37"/><path d="M6 4l3 3-3 3" fill="none" stroke="#fff" stroke-width="1.8"/></svg>Values</li>
  <li><svg width="14" height="14" viewBox="0 0 14 14"><circle cx="7" cy="7" r="7" fill="#7aab37"/><path d="M6 4l3 3-3 3" fill="none" stroke="#fff" stroke-width="1.8"/></svg>Spiritual Life</li>
</ul>
<a class="btn abs" style="left:645px;top:1822px;width:198px;height:53px">Learn More</a>

<!-- research -->
<section class="research">
<h2 class="heading abs" style="top:2072px;font-size:41px">Research Projects</h2>
<p class="intro abs" style="top:2126px">Lorem ipsum dolor sit amet, consectetur adipiscing elit, sed do eiusmod<br>tempor incididunt ut labore et dolore magna aliqua.</p>
<div class="project abs" style="left:112px"><div class="photo" role="img" aria-label="Hand using a calculator" style="background:linear-gradient(160deg,#8a7e72,#d8d4cf 50%,#3b4450)"></div><div class="label">Lorem ipsum dolor sit</div></div>
<div class="project abs" style="left:358px"><div class="photo" role="img" aria-label="Data charts on a digital screen" style="background:linear-gradient(160deg,#c9d3dc,#6f8296 50%,#c98b94)"></div><div class="label">Lorem ipsum dolor sit</div></div>
<div class="project abs active" style="left:605px"><div class="photo" role="img" aria-label="Colleagues reviewing work on a laptop" style="background:linear-gradient(160deg,#e8e4dc,#b59a72 50%,#d9d6d0)"></div><div class="label">Lorem ipsum dolor sit</div></div>
<div class="project abs" style="left:850px"><div class="photo" role="img" aria-label="Financial charts and a calculator on a desk" style="background:linear-gradient(160deg,#2d3a4e,#dbe2ea 55%,#6a8db0)"></div><div class="label">Lorem ipsum dolor sit</div></div>
<div class="arrow abs" style="left:49px;top:2323px;background:#6f9bbf"><svg width="14" height="14" viewBox="0 0 14 14"><path d="M9 2 4 7l5 5" fill="none" stroke="#fff" stroke-width="2"/></svg></div>
<div class="arrow abs" style="left:1099px;top:2323px;background:#6f9bbf"><svg width="14" height="14" viewBox="0 0 14 14"><path d="M5 2l5 5-5 5" fill="none" stroke="#fff" stroke-width="2"/></svg></div>
</section>

<!-- faq -->
<section class="faq abs"></section>
<h2 class="heading abs" style="top:2678px;font-size:41px">FAQs</h2>
<p class="intro abs" style="top:2733px">Lorem ipsum dolor sit amet, consectetur adipiscing elit, sed do eiusmod<br>tempor incididunt ut labore et dolore magna aliqua.</p>
<div class="faq-item abs" style="top:2822px">What makes this project unique?<span class="plus"></span></div>
<div class="faq-item abs" style="top:2891px">Does this project assume that the impact of religion is always positive?<span class="plus"></span></div>
<div class="faq-item abs" style="top:2960px">How can I collaborate?<span class="plus"></span></div>
<div class="faq-item abs" style="top:3028px">Will Harrowgate U faculty lead all projects?<span class="plus"></span></div>

<!-- footer -->
<footer class="site-footer abs"></footer>
<div class="footer-brand abs"><span class="mark"></span><span class="name">Wellness, Meaning, and the Inner Journey<br>The Research Program</span></div>
<div class="contact abs">
  <span><svg width="10" height="13" viewBox="0 0 10 13"><path d="M5 0a5 5 0 0 1 5 5c0 3-5 8-5 8S0 8 0 5a5 5 0 0 1 5-5z" fill="#fff"/><circle cx="5" cy="5" r="2" fill="#135a96"/></svg>Address 204 Alder Bend Rd, Fernhill, OR, 97321</span>
  <span><svg width="12" height="12" viewBox="0 0 12 12"><path d="M2 0l3 3-1.5 1.5a7 7 0 0 0 4 4L9 7l3 3-2 2C5 12 0 7 0 2z" fill="#fff"/></svg>P: 555-014-2290</span>
  <span><svg width="14" height="11" viewBox="0 0 14 11"><rect width="14" height="11" rx="1" fill="#fff"/><path d="M1 1l6 5 6-5" fill="none" stroke="#135a96" stroke-width="1.4"/></svg>Email - info@wmij-research.org</span>
</div>
<nav class="foot-nav abs"><span>Home</span><span>People</span><span>Research Projects</span><span>FAQs</span><span>Contact us</span></nav>
<p class="copy abs">© 2021 All Rights Reserved</p>

</body>
</html>
```